Business Cards for new orthopaedic surgery practice

My husband and I are starting our own orthopaedic surgery practice. We are looking for a business card that is uniform, but one will have my name/title and the other will have his. You can just create one design with my name on it for now. But when I choose your design as the winning design I will ask that you add another copy with his name/title.

We are looking for classy, simple, elite all in one. We like dark blues/a little gold/yellow. Something that goes with our logo. We want our logo incorporated. Here is all the info you need:
Business name: RV Bone & Vitality Center
Location: 38517 North Willowmere Ave
Palm Harbor, FL 34683
Phone: 954-218-4063
Fax: 954-582-7341
Email: info@myrvbonecare.example

Names: Lydia Vance, M.D.
Board Certified Hand and Upper Extremity Surgeon

Ebo Dansu, M.D.
Board Certified Hip & Knee Replacement/General Orthopaedic Surgeon

Can decide what you want to put on the back. Maybe a slogan:
Grounded in Care. Centered on You

I am just going to upload our logo. The only thing is if we select you as the winning design, the location, and phone numbers may change. We will need your help to update that once fully solidified.

Industry/Entity Type

Medical

Contact Information for Business Card

Colors
0054AA
0677BA
7BADD7
CADEEF
E8F1F8
0094D4
00A9DD
6FCCEA
C7EBF8
E9F6FB

Requirements
Must have
• class, appeal,
Should not have
• We want to air on the side of masculine if we are looking at masculine vs. feminine feel. But we still want it classy, sophisticated, and something we will love

```html
<!DOCTYPE html>
<html lang="en">
<head>
<meta charset="utf-8">
<title>RV Bone &amp; Vitality Center — Business Card</title>
<link rel="stylesheet" href="https://fonts.googleapis.com/css2?family=Cinzel:wght@700&family=Arimo:wght@400&display=swap">
<style>
  :root {
    --navy: #1c2a52;
    --navy-light: #283b64;
    --navy-deep: #1a284d;
    --gold: #c9a25a;
    --ink: #3a3a3a;
    --paper: #ffffff;
    --backdrop: #e4e4e4;
    --mark-tone: #4a5f8c;
  }
  * { box-sizing: border-box; margin: 0; padding: 0; }
  html, body { width: 1200px; height: 1200px; overflow: hidden; }
  body {
    background: var(--backdrop);
    font-family: "Arimo", Arial, sans-serif;
    position: relative;
  }
  .card {
    position: absolute;
    left: 200px;
    width: 800px;
    height: 460px;
  }
  .card-front { top: 100px; background: var(--paper); }
  .card-back {
    top: 640px;
    background: linear-gradient(180deg, var(--navy-light) 0%, var(--navy-deep) 100%);
  }

  /* Front: brand block */
  .brand-seal {
    position: absolute;
    left: 117px; top: 100px;
    width: 200px; height: 200px;
    border: 2px solid var(--gold);
    border-radius: 50%;
    display: flex; align-items: center; justify-content: center;
    text-align: center;
  }
  .brand-name {
    font-family: "Cinzel", Georgia, serif;
    font-weight: 700;
    color: var(--navy);
    font-size: 21px;
    line-height: 1.25;
    letter-spacing: 1px;
  }
  .divider {
    position: absolute;
    left: 356px; top: 80px;
    width: 2px; height: 250px;
    background: #d6d6d6;
  }
  .details {
    position: absolute;
    left: 387px; top: 88px;
    color: var(--ink);
  }
  .person-name {
    font-family: "Cinzel", Georgia, serif;
    font-weight: 700;
    font-size: 26px;
    color: var(--navy);
    letter-spacing: 1px;
    line-height: 1.1;
  }
  .person-title {
    color: var(--gold);
    font-size: 18px;
    line-height: 23px;
    margin-top: 4px;
  }
  .address {
    font-size: 19px;
    line-height: 25px;
    margin-top: 13px;
  }
  .contact-list { list-style: none; margin-top: 12px; }
  .contact-list li {
    display: flex; align-items: center;
    font-size: 18.5px;
    line-height: 24px;
  }
  .contact-list svg { width: 18px; height: 18px; margin-right: 11px; fill: var(--navy); }

  .footer-band {
    position: absolute;
    left: 0; top: 378px;
    width: 800px; height: 41px;
    display: flex;
  }
  .footer-web {
    width: 626px;
    background: var(--navy);
    color: #fff;
    font-size: 18px;
    display: flex; align-items: center;
    padding-left: 121px;
  }
  .footer-spot {
    width: 49px;
    background: var(--paper);
    display: flex; align-items: center; justify-content: center;
  }
  .footer-spot span {
    width: 22px; height: 22px; border-radius: 50%;
    background: var(--navy);
  }
  .footer-accent { flex: 1; background: var(--gold); }

  /* Back */
  .back-mark {
    position: absolute;
    left: 0; right: 0; top: 120px;
    text-align: center;
    font-family: "Cinzel", Georgia, serif;
    font-weight: 700;
    color: var(--mark-tone);
    font-size: 46px;
    line-height: 1.3;
    letter-spacing: 2px;
  }
  .slogan {
    position: absolute;
    left: 0; right: 0; top: 392px;
    text-align: center;
    color: var(--gold);
    font-size: 19px;
    letter-spacing: 3.6px;
    text-transform: uppercase;
  }
</style>
</head>
<body>
  <section class="card card-front" aria-label="Business card front">
    <div class="brand-seal">
      <p class="brand-name">RV Bone<br>&amp; Vitality<br>Center</p>
    </div>
    <div class="divider"></div>
    <div class="details">
      <h1 class="person-name">LYDIA VANCE, M.D.</h1>
      <p class="person-title">Board Certified Hand and<br>Upper Extremity Surgeon</p>
      <p class="address">38517 North Willowmere Ave<br>Palm Harbor, FL 34683</p>
      <ul class="contact-list">
        <li>
          <svg viewBox="0 0 24 24" aria-hidden="true"><path d="M6.6 10.8c1.4 2.8 3.8 5.1 6.6 6.6l2.2-2.2c.3-.3.7-.4 1-.2 1.1.4 2.3.6 3.6.6.6 0 1 .4 1 1V20c0 .6-.4 1-1 1C10.6 21 3 13.4 3 4c0-.6.4-1 1-1h3.5c.6 0 1 .4 1 1 0 1.3.2 2.5.6 3.6.1.3 0 .7-.2 1z"/></svg>
          954-218-4063
        </li>
        <li>
          <svg viewBox="0 0 24 24" aria-hidden="true"><path d="M6 2h9l3 3v5H6zM3 11h18v9H3zm3 5v2h12v-2zm0-3v1.5h12V13z"/></svg>
          954-582-7341
        </li>
        <li>
          <svg viewBox="0 0 24 24" aria-hidden="true"><path d="M3 5h18v14H3zm2 2v.5l7 5 7-5V7l-7 5z"/></svg>
          info@myrvbonecare.example
        </li>
      </ul>
    </div>
    <div class="footer-band">
      <div class="footer-web">www.myrvbonecare.example</div>
      <div class="footer-spot"><span></span></div>
      <div class="footer-accent"></div>
    </div>
  </section>

  <section class="card card-back" aria-label="Business card back">
    <p class="back-mark">RV Bone &amp;<br>Vitality Center</p>
    <p class="slogan">Grounded in care. Centered on you</p>
  </section>
</body>
</html>
```